Business Card Design For Office Furniture Clearance Company

Kestrel Office Clearance - our company name pretty much explains what we do, we clear offices for high end clients, mainly plc's and large international companies.

We require a nice looking business card that displays professionalism but without being too serious.

It would be nice to see just a little more than a conventional boring business card, make sure you add some flare.

Industry/Entity Type

Office Furniture

Contact Information for Business Card

CARD 1

Mark Holloway
Director
mark@kestrelofficeclearance.co.uk
m: 07700 153928

t: 01632 960418
www.kestrelofficeclearance.co.uk

Kestrel Office Clearance
Unit K4 B
2-8 Fenwick Lane
Ashcombe
Westbrook
ZZ9 4QT

Office clearances at no cost… hard to beat that offer.

CARD 2

Peter Radford
Director
peter@kestrelofficeclearance.co.uk
m: 07700 382615

t: 01632 960418

Kestrel Office Clearance
Unit K4 B
2-8 Fenwick Lane
Ashcombe
Westbrook
ZZ9 4QT

Font styles to use
Sans Serif

Requirements
Must have
• A white background - as we have a blue logo.
Nice to have
• Nice use of the logo - play around with this and dissect it.

```html
<!DOCTYPE html>
<html lang="en">
<head>
<meta charset="utf-8">
<title>Kestrel Office Clearance – Business Cards</title>
<link rel="stylesheet" href="https://fonts.googleapis.com/css2?family=Source+Sans+3:wght@400;600;700&display=swap">
<style>
  :root {
    --brand-blue: #0a7bbf;
    --brand-blue-deep: #06639e;
    --card-white: #ffffff;
    --text-on-blue: #ffffff;
    --page-bg: #eceff2;
    --card-shadow: rgba(20, 40, 60, 0.12);
  }
  * { box-sizing: border-box; margin: 0; padding: 0; }
  html, body {
    width: 1200px;
    height: 900px;
    overflow: hidden;
    background: var(--page-bg);
    font-family: "Source Sans 3", "Segoe UI", Arial, sans-serif;
  }
  .canvas { position: relative; width: 1200px; height: 900px; }

  .card {
    position: absolute;
    width: 556px;
    height: 342px;
    background: var(--card-white);
    box-shadow: 0 6px 24px var(--card-shadow);
  }
  .card--front { left: 238px; top: 62px; }
  .card--back  { left: 458px; top: 519px; width: 559px; }

  .band {
    position: absolute;
    left: 0; right: 0;
    top: 69px;
    height: 204px;
    background: var(--brand-blue);
    overflow: hidden;
    color: var(--text-on-blue);
  }

  /* Front card */
  .brand-disc {
    position: absolute;
    left: 0; top: 0;
    width: 206px; height: 204px;
  }
  .brand-disc__name {
    position: absolute;
    left: 28px; top: 84px;
    width: 150px;
    text-align: center;
    font-weight: 700;
    font-size: 26px;
    color: var(--brand-blue);
  }
  .person {
    position: absolute;
    left: 236px; top: 32px;
  }
  .person__name { font-size: 20px; font-weight: 600; line-height: 1.15; }
  .person__role { font-size: 15px; font-weight: 400; line-height: 1.2; }
  .contact-list {
    list-style: none;
    position: absolute;
    left: 236px; top: 91px;
  }
  .contact-list li {
    display: flex;
    align-items: center;
    gap: 9px;
    font-size: 15.5px;
    line-height: 20.5px;
  }
  .contact-list svg { width: 12px; height: 12px; flex: none; fill: var(--text-on-blue); }

  /* Back card */
  .corner-disc {
    position: absolute;
    left: 439px; top: -33px;
    width: 190px; height: 190px;
    border-radius: 50%;
    background: var(--card-white);
  }
  .company {
    position: absolute;
    left: 24px; top: 83px;
  }
  .company__name { font-size: 20px; font-weight: 700; line-height: 1.2; }
  .company__address { font-size: 15px; line-height: 1.3; margin-top: 4px; }
  .company__tagline { font-size: 19.5px; line-height: 1.2; margin-top: 13px; }
</style>
</head>
<body>
<main class="canvas">

  <section class="card card--front" aria-label="Business card front">
    <div class="band">
      <svg class="brand-disc" viewBox="0 0 206 204" aria-hidden="true">
        <circle cx="102" cy="102" r="100" fill="#ffffff"/>
      </svg>
      <span class="brand-disc__name">Kestrel</span>

      <div class="person">
        <p class="person__name">Mark Holloway</p>
        <p class="person__role">Director</p>
      </div>

      <ul class="contact-list">
        <li>
          <svg viewBox="0 0 12 12" aria-hidden="true"><path d="M3.5 0.5h5a1 1 0 0 1 1 1v9a1 1 0 0 1-1 1h-5a1 1 0 0 1-1-1v-9a1 1 0 0 1 1-1zm0.3 1.3v7.4h4.4V1.8zM6 9.7a0.6 0.6 0 1 0 0 1.2a0.6 0.6 0 0 0 0-1.2z"/></svg>
          07700 153928
        </li>
        <li>
          <svg viewBox="0 0 12 12" aria-hidden="true"><path d="M2.6 0.8l1.8-0.3 1 2.6-1.2 1a6.5 6.5 0 0 0 3.7 3.7l1-1.2 2.6 1-0.3 1.8c-0.1 0.6-0.7 1-1.3 1C4.6 10.2 1.8 7.4 1.6 2.1c0-0.6 0.4-1.2 1-1.3z"/></svg>
          01632 960418
        </li>
        <li>
          <svg viewBox="0 0 12 12" aria-hidden="true"><path d="M1 2.5h10v7H1zm1 1v0.4l4 2.6 4-2.6V3.5zm0 1.6v3.4h8V5.1L6 7.7z"/></svg>
          mark@kestrelofficeclearance.co.uk
        </li>
        <li>
          <svg viewBox="0 0 12 12" aria-hidden="true"><path d="M6 0.5a5.5 5.5 0 1 0 0 11a5.5 5.5 0 0 0 0-11zm-1 2l1.5 1-0.5 1.5 1.5 1-1 2.5-1-1.5-1.5-0.5 0-2zm3 0.2l1.6 1.3-0.6 1.2-1.2-0.8z"/></svg>
          www.kestrelofficeclearance.co.uk
        </li>
      </ul>
    </div>
  </section>

  <section class="card card--back" aria-label="Business card back">
    <div class="band">
      <div class="corner-disc" aria-hidden="true"></div>
      <div class="company">
        <p class="company__name">Kestrel Office Clearance</p>
        <p class="company__address">Unit K4 B,2-8 Fenwick Lane,Ashcombe,Westbrook,ZZ9 4QT</p>
        <p class="company__tagline">Office clearances at no cost… hard to beat that offer.</p>
      </div>
    </div>
  </section>

</main>
</body>
</html>
```